Business Card Design for Occupational Medicine Start Up Company

We need to design a professional business card. We are a healthcare company providing occupational medicine services to blue collar industries. We are professional, efficient and high quality service providers.

Target Market(s)

Blue Collar Industry: Shipbuilding, Ports, Trucking Companies; The Executives and Safety Officers for these companies

Industry/Entity Type

Healthcare

Contact Information for Business Card

Logo, Name, Title, Email, Phone

Other font styles liked:
• Please match our Brand Guide

Requirements
Must have
• Our Company Colors and Logo

```html
<!DOCTYPE html>
<html lang="en">
<head>
<meta charset="utf-8">
<title>Shiftwell Business Card</title>
<link href="https://fonts.googleapis.com/css2?family=Roboto:ital,wght@0,400;0,500;0,700;1,400&display=swap" rel="stylesheet">
<style>
  :root {
    --navy: #283583;
    --blue-deep: #1f4f96;
    --blue-light: #2a9ad6;
    --orange: #f6a834;
    --white: #ffffff;
    --stage: #e9ebef;
  }
  html, body {
    margin: 0;
    width: 1200px;
    height: 900px;
    overflow: hidden;
    background: var(--stage);
    font-family: "Roboto", Arial, sans-serif;
  }
  .canvas {
    position: relative;
    width: 1200px;
    height: 900px;
  }
  .card {
    position: absolute;
    left: 320px;
    width: 560px;
    height: 320px;
    border-radius: 18px;
    overflow: hidden;
    box-shadow: 0 10px 28px rgba(20, 30, 70, 0.22);
  }
  .card--front { top: 100px; background: var(--white); }
  .card--back { top: 480px; background: var(--navy); }

  .front-shape { position: absolute; inset: 0; }

  .holder {
    position: absolute;
    left: 30px;
    top: 30px;
    color: var(--white);
  }
  .holder__name {
    margin: 0;
    font-weight: 700;
    font-size: 24px;
    letter-spacing: 0.5px;
    color: var(--orange);
    text-transform: uppercase;
  }
  .holder__title {
    margin: 2px 0 0;
    font-style: italic;
    font-size: 13px;
  }

  .contact {
    position: absolute;
    left: 30px;
    bottom: 34px;
    margin: 0;
    padding: 0;
    list-style: none;
    color: var(--white);
    font-size: 13px;
    line-height: 21px;
  }
  .contact__item { display: flex; align-items: center; gap: 7px; }
  .contact__icon { width: 11px; height: 11px; flex: none; }

  .brand {
    position: absolute;
    display: flex;
    align-items: center;
    gap: 10px;
  }
  .brand--front { left: 290px; top: 160px; }
  .brand--back { left: 50%; top: 50%; transform: translate(-50%, -50%); }
  .brand__dot {
    width: 20px;
    height: 20px;
    border-radius: 50%;
    background: var(--orange);
  }
  .brand__name {
    font-weight: 500;
    font-size: 28px;
    letter-spacing: 2px;
    text-transform: uppercase;
    white-space: nowrap;
  }
  .brand--front .brand__name { color: var(--navy); }
  .brand--back .brand__name { color: var(--white); font-size: 44px; letter-spacing: 3px; }
</style>
</head>
<body>
<main class="canvas">

  <section class="card card--front" aria-label="Card front">
    <svg class="front-shape" width="560" height="320" viewBox="0 0 560 320">
      <defs>
        <linearGradient id="panelGradient" x1="0" y1="0" x2="1" y2="1">
          <stop offset="0" stop-color="var(--blue-deep)"/>
          <stop offset="1" stop-color="var(--blue-light)"/>
        </linearGradient>
      </defs>
      <rect width="560" height="320" fill="url(#panelGradient)"/>
      <circle cx="470" cy="235" r="240" fill="var(--white)"/>
      <circle cx="470" cy="235" r="248" fill="none" stroke="var(--orange)" stroke-width="4"/>
    </svg>

    <div class="holder">
      <p class="holder__name">Daniel Morrow</p>
      <p class="holder__title">Director</p>
    </div>

    <ul class="contact">
      <li class="contact__item">
        <svg class="contact__icon" viewBox="0 0 12 12"><path d="M2 1h3l1 3-2 1a7 7 0 0 0 3 3l1-2 3 1v3c-6 0-10-4-10-9z" fill="var(--orange)"/></svg>
        (555)010 2841
      </li>
      <li class="contact__item">
        <svg class="contact__icon" viewBox="0 0 12 12"><rect x="0.5" y="2" width="11" height="8" fill="var(--orange)"/><path d="M0.5 2l5.5 4 5.5-4" fill="none" stroke="var(--white)" stroke-width="1"/></svg>
        hello@shiftwell.com
      </li>
      <li class="contact__item">
        <svg class="contact__icon" viewBox="0 0 12 12"><circle cx="6" cy="6" r="5.5" fill="var(--orange)"/><path d="M0.5 6h11M6 0.5c-3 3-3 8 0 11M6 0.5c3 3 3 8 0 11" fill="none" stroke="var(--white)" stroke-width="0.8"/></svg>
        www.shiftwell.com
      </li>
    </ul>

    <div class="brand brand--front">
      <span class="brand__dot"></span>
      <span class="brand__name">Shiftwell</span>
    </div>
  </section>

  <section class="card card--back" aria-label="Card back">
    <div class="brand brand--back">
      <span class="brand__dot"></span>
      <span class="brand__name">Shiftwell</span>
    </div>
  </section>

</main>
</body>
</html>
```